Business Card Design Project

We need a new fresh business card for our business. There are multiple services we offer and we need a fresh corporate card that represents us better. We start from cleaning carpet and tiles, to upholstery and curtains, to completely clean all contents and building materials after a fire, or completely dry out a home or business after a major or minor flood event. We are open to all concepts as we want to create a new look, maybe even logo, signage, vehicle signage, uniforms.
We are open to new colours etc.

Go to www.brolvaquincare.com.au for current logo and all other past ideas

Target Market(s)

Everyone is our possible client but we are targeting more coorporate

Industry/Entity Type

Building

```html
<!DOCTYPE html>
<html lang="en">
<head>
<meta charset="utf-8">
<title>Brolvaquin Care – Business Card</title>
<link href="https://fonts.googleapis.com/css2?family=Exo+2:wght@400;500;600;700&display=swap" rel="stylesheet">
<style>
  :root {
    --page-bg: #e9eaec;
    --card-white: #ffffff;
    --card-blue: #1f5aa6;
    --accent-magenta: #e0187a;
    --text-light: #ffffff;
    --brand-blue: #1f5aa6;
  }
  * { margin: 0; padding: 0; box-sizing: border-box; }
  html, body {
    width: 1200px; height: 899px; overflow: hidden;
    background: var(--page-bg);
    font-family: "Exo 2", sans-serif;
  }
  .business-card {
    position: absolute; left: 180px; top: 210px;
    width: 840px; height: 480px;
    border-radius: 40px; overflow: hidden;
    background: var(--card-white);
    box-shadow: 0 6px 18px rgba(0,0,0,0.18);
  }
  .card-shapes { position: absolute; inset: 0; }
  .brand-lockup {
    position: absolute; left: 50px; top: 178px;
    display: flex; align-items: center; gap: 18px;
  }
  .brand-name {
    font-size: 40px; font-weight: 700; color: var(--brand-blue);
    letter-spacing: 0.5px; line-height: 1;
  }
  .brand-dot {
    width: 70px; height: 70px; border-radius: 50%;
    background: var(--accent-magenta);
  }
  .contact-block {
    position: absolute; left: 575px; top: 84px;
    color: var(--text-light);
  }
  .person-name {
    font-size: 22px; font-weight: 500; letter-spacing: 1.5px; text-transform: uppercase;
  }
  .person-title { font-size: 15px; font-weight: 400; margin-top: 2px; letter-spacing: 0.5px; }
  .office-address {
    font-size: 18px; font-weight: 400; line-height: 26px; margin-top: 42px; letter-spacing: 0.3px;
  }
  .contact-list { list-style: none; margin-top: 46px; margin-left: -20px; }
  .contact-list li {
    display: flex; align-items: center; gap: 10px;
    font-size: 13px; letter-spacing: 0.8px; height: 28px;
  }
  .contact-list svg { width: 13px; height: 13px; flex: none; }
</style>
</head>
<body>
  <div class="business-card">
    <svg class="card-shapes" viewBox="0 0 840 480" width="840" height="480" aria-hidden="true">
      <path class="accent-swoosh" fill="var(--accent-magenta)"
        d="M476 0 L840 0 L840 480 L0 480 L0 408 C240 392 538 292 538 142 C538 82 518 30 476 0 Z"/>
      <path class="blue-panel" fill="var(--card-blue)"
        d="M498 0 L840 0 L840 480 L0 480 L0 422 C250 404 562 302 562 142 C562 80 540 30 498 0 Z"/>
    </svg>

    <div class="brand-lockup">
      <span class="brand-name">Brolvaquin Care</span>
      <span class="brand-dot"></span>
    </div>

    <div class="contact-block">
      <p class="person-name">Marcus Delaney</p>
      <p class="person-title">Managing Director</p>
      <p class="office-address">214 9th floor,Harbour Crest<br>Road QLD</p>
      <ul class="contact-list">
        <li>
          <svg viewBox="0 0 16 16"><path fill="#fff" d="M3 1l3 3-1.5 2c1 2 2.5 3.5 4.5 4.5L11 9l3 3-2 2.5C6 14 2 10 1.5 3z"/></svg>
          012 555 0148
        </li>
        <li>
          <svg viewBox="0 0 16 16"><rect x="4" y="1" width="8" height="14" rx="1.5" fill="none" stroke="#fff" stroke-width="1.6"/><circle cx="8" cy="12.5" r="0.9" fill="#fff"/></svg>
          012 555 0149
        </li>
        <li>
          <svg viewBox="0 0 16 16"><rect x="4" y="1" width="8" height="5" fill="#fff"/><rect x="1" y="6" width="14" height="6" rx="1" fill="#fff"/><rect x="4" y="10" width="8" height="5" fill="#fff" stroke="#1f5aa6" stroke-width="1"/></svg>
          012 555 0150
        </li>
        <li>
          <svg viewBox="0 0 16 16"><rect x="1" y="3" width="14" height="10" rx="1" fill="#fff"/><path d="M1.5 3.5L8 9l6.5-5.5" fill="none" stroke="#1f5aa6" stroke-width="1.2"/></svg>
          hello@brolvaquincare.com.au
        </li>
        <li>
          <svg viewBox="0 0 16 16"><circle cx="8" cy="8" r="6.5" fill="none" stroke="#fff" stroke-width="1.4"/><ellipse cx="8" cy="8" rx="2.8" ry="6.5" fill="none" stroke="#fff" stroke-width="1.2"/><path d="M1.5 8h13" stroke="#fff" stroke-width="1.2"/></svg>
          www.brolvaquincare.com.au
        </li>
      </ul>
    </div>
  </div>
</body>
</html>
```